Mental Health care Company in Washington DC

We are a new mental health care services provider in Washington DC. Please look at these sites.
https://brightwaterfamilysupport.com
https://www.quietharborinc.com
https://willowgate-dc.org/
https://www.tidepathdc.com
https://www.thelanternofdc.com

```html
<!DOCTYPE html>
<html lang="en">
<head>
<meta charset="utf-8">
<title>Calmora Health Services</title>
<link href="https://fonts.googleapis.com/css2?family=Poppins:wght@400;500;600;700;800&display=swap" rel="stylesheet">
<style>
:root{
  --navy:#13264b;
  --navy-deep:#0f2247;
  --teal:#a4dade;
  --orange:#f6a25b;
  --ink:#1d1d1f;
  --white:#ffffff;
}
*{box-sizing:border-box;margin:0;padding:0}
html,body{width:1200px;height:4487px;overflow:hidden}
body{font-family:"Poppins",sans-serif;color:var(--ink);background:var(--white);position:relative}
.abs{position:absolute}
.fill{display:block}
.btn{position:absolute;display:flex;align-items:center;justify-content:center;background:var(--orange);color:var(--white);font-weight:600;border-radius:8px;box-shadow:0 3px 6px rgba(0,0,0,.12)}
.mark{width:22px;height:22px;border-radius:50%;background:var(--orange);display:inline-block;flex:none}
.section-title{position:absolute;left:0;width:1200px;text-align:center;font-weight:700;font-size:37px;color:var(--navy)}
.section-mark{position:absolute;left:589px;width:22px;height:22px;border-radius:50%;background:var(--orange)}

/* header */
.header{position:absolute;left:0;top:0;width:1200px;height:132px;background:var(--white);z-index:3}
.header-bar{position:absolute;left:580px;top:0;width:620px;height:62px;background:var(--teal);clip-path:polygon(22px 0,100% 0,100% 100%,0 100%)}
.brand{position:absolute;left:74px;top:48px;display:flex;align-items:center;gap:10px;font-weight:600;font-size:26px;color:var(--navy);white-space:nowrap}
.phone{position:absolute;left:625px;top:16px;font-weight:600;font-size:23px;color:var(--navy);display:flex;align-items:center;gap:10px}
.appt{left:867px;top:5px;width:260px;height:52px;background:var(--navy-deep);font-size:16px;border-radius:8px;color:var(--orange)}
.nav{position:absolute;top:88px;left:0;font-weight:600;font-size:17px;color:var(--navy)}
.nav span{position:absolute;white-space:nowrap}
.nav .active{color:var(--orange);text-decoration:underline;text-underline-offset:5px}

/* hero */
.hero{position:absolute;left:0;top:132px;width:1200px;height:740px}
.hero-title{position:absolute;left:76px;top:150px;font-weight:800;font-size:64px;line-height:70px;color:var(--navy);white-space:nowrap}
.hero-title span{display:block;color:#5b5b5b;font-size:62px}
.hero-text{position:absolute;left:75px;top:300px;width:420px;font-size:19px;line-height:31px;color:#333}
.hero-btn{left:77px;top:416px;width:200px;height:50px;font-size:16px}
.dots{position:absolute;left:1128px;top:578px}
.dots i{display:block;width:8px;height:8px;border-radius:50%;background:var(--navy);margin-bottom:14px}
.dots i:first-child{background:var(--orange)}

/* services */
.svc{position:absolute;top:996px;width:242px;height:236px;border-radius:6px}
.svc.active{outline:4px solid var(--orange);outline-offset:-2px}
.svc-label{position:absolute;top:1258px;width:242px;text-align:center;font-weight:600;font-size:16px;color:#222}
.arrow{position:absolute;font-size:40px;color:#2a2a2a;font-weight:400;line-height:1}

/* about & why */
.copy{position:absolute;font-size:18px;line-height:29.5px;color:#1f1f1f}
.h2{position:absolute;font-weight:700;font-size:38px;line-height:47px;color:var(--navy);white-space:nowrap}
.h2 .mark{position:absolute;left:-42px;top:12px}

/* stories */
.story{position:absolute;top:2880px;height:282px;background:var(--white);text-align:center;padding:0 6px}
.story.faded{background:#f5f5f5;opacity:.85}
.quote-mark{font-weight:800;font-size:90px;line-height:70px;color:#ddd;margin-top:20px;height:40px}
.story p{font-size:16px;line-height:26px;color:#444;margin-top:4px}
.story .name{font-weight:600;color:var(--orange);margin-top:14px;font-size:17px}
.avatar{position:absolute;top:3115px;width:82px;height:82px;border-radius:50%;background:linear-gradient(160deg,#a8b6c4,#6f7d8a)}

/* partners */
.partner{position:absolute;top:3477px;width:165px;height:108px;border:2px solid #cfcfcf;background:var(--white);display:flex;align-items:center;justify-content:center}
.partner i{display:block;width:110px;height:44px;border-radius:6px;background:#d9dde2}

/* newsletter */
.news-title{position:absolute;left:0;top:3765px;width:1200px;text-align:center;font-weight:700;font-size:37px;color:var(--white)}
.news-text{position:absolute;left:120px;top:3840px;width:960px;text-align:center;font-size:18px;line-height:30px;color:var(--white)}
.email{position:absolute;left:223px;top:3930px;width:580px;height:54px;background:var(--white);border-radius:8px 0 0 8px;font-size:15px;color:#333;padding:17px 16px}
.submit{left:775px;top:3924px;width:207px;height:67px;font-size:19px;border-radius:8px}

/* footer */
.foot-brand{position:absolute;left:77px;top:4215px;width:340px;display:flex;align-items:center;gap:12px;font-weight:600;font-size:32px;line-height:38px;color:var(--navy)}
.copyright{position:absolute;left:80px;top:4320px;width:295px;text-align:center;font-size:15px;line-height:26px;color:#222}
.social{position:absolute;top:4395px;width:24px;height:24px;border-radius:50%;background:var(--navy)}
.foot-head{position:absolute;font-weight:600;font-size:21px;color:var(--navy)}
.links{position:absolute;left:492px;top:4222px;font-size:15px;line-height:36px;color:#222;list-style:none}
.contact{position:absolute;left:767px;top:4235px;font-size:15px;line-height:26px;color:#222;list-style:none}
.contact li{position:relative;padding-left:34px;margin-bottom:10px}
.contact svg{position:absolute;left:0;top:5px}
</style>
</head>
<body>

<header class="header">
  <div class="header-bar"></div>
  <div class="brand"><span class="mark"></span>Calmora Health Services</div>
  <div class="phone">
    <svg width="18" height="18" viewBox="0 0 24 24"><path fill="#13264b" d="M6.6 10.8a15.1 15.1 0 0 0 6.6 6.6l2.2-2.2c.3-.3.7-.4 1-.2 1.1.4 2.3.6 3.6.6.6 0 1 .4 1 1V20c0 .6-.4 1-1 1A17 17 0 0 1 3 4c0-.6.4-1 1-1h3.5c.6 0 1 .4 1 1 0 1.3.2 2.5.6 3.6.1.3 0 .7-.2 1z"/></svg>
    +1-202-555-0147
  </div>
  <div class="btn appt">MAKE AND APPOINTMENT</div>
  <nav class="nav">
    <span class="active" style="left:495px">Home</span>
    <span style="left:590px">About Us</span>
    <span style="left:713px">Services</span>
    <span style="left:833px">Blog</span>
    <span style="left:915px">Careers</span>
    <span style="left:1030px">Contact Us</span>
  </nav>
</header>

<section class="hero">
  <div class="abs fill" role="img" aria-label="Faded photo of a hand placing a colourful puzzle piece" style="left:0;top:0;width:1200px;height:740px;background:linear-gradient(120deg,#e9e3df 0%,#efe6da 35%,#e4e5ea 65%,#eceef1 100%)"></div>
  <svg class="abs" style="left:0;top:650px" width="1200" height="92" viewBox="0 0 1200 92"><path d="M0 60 C200 0 420 10 640 40 C860 70 1040 40 1200 10 L1200 92 L0 92Z" fill="#fff"/></svg>
  <h1 class="hero-title">Calmora Health<span>Services</span></h1>
  <p class="hero-text">Nemo enim ipsam voluptatem quia voluptas sit aspernatur aut odit aut fugit, sed quia consequuntur explicabo.</p>
  <div class="btn hero-btn">ENROLL NOW</div>
  <div class="abs" role="img" aria-label="Photo of a mother and daughter laughing outdoors" style="left:772px;top:73px;width:138px;height:208px;border-radius:69px 69px 0 0;background:linear-gradient(160deg,#4f7e55,#2f4f3a)"></div>
  <div class="abs" role="img" aria-label="Photo of two hands clasped in support" style="left:510px;top:281px;width:262px;height:152px;border-radius:76px 0 0 76px;background:linear-gradient(120deg,#e8b48c,#9a5a3a)"></div>
  <div class="abs" role="img" aria-label="Photo of a counsellor shaking hands with a client" style="left:910px;top:281px;width:260px;height:152px;border-radius:0 76px 76px 0;background:linear-gradient(120deg,#6fa6b6,#2e5f76)"></div>
  <div class="abs" role="img" aria-label="Photo of a nurse talking with a patient" style="left:772px;top:433px;width:138px;height:210px;border-radius:0 0 69px 69px;background:linear-gradient(160deg,#3d8c8a,#7a4b37)"></div>
  <div class="dots"><i></i><i></i><i></i><i></i></div>
</section>

<span class="section-mark" style="top:890px"></span>
<h2 class="section-title" style="top:912px">Our Services</h2>
<span class="arrow" style="left:40px;top:1092px">&#8249;</span>
<span class="arrow" style="left:1138px;top:1092px">&#8250;</span>
<div class="svc active" role="img" aria-label="Photo of a doctor caring for a senior patient" style="left:75px;background:linear-gradient(150deg,#c9c2bd,#6b3f6e)"></div>
<div class="svc" role="img" aria-label="Photo of open hands beneath a head silhouette" style="left:345px;background:linear-gradient(150deg,#d8c5b3,#8a5c3f)"></div>
<div class="svc" role="img" aria-label="Photo of a group therapy conversation" style="left:615px;background:linear-gradient(150deg,#b9c3b7,#6e7c86)"></div>
<div class="svc" role="img" aria-label="Photo of a woman meditating" style="left:885px;background:linear-gradient(150deg,#8b9794,#3f4a4a)"></div>
<div class="svc-label" style="left:75px">MEDICAL SERVICES</div>
<div class="svc-label" style="left:345px">BEHAVIORAL HEALTH</div>
<div class="svc-label" style="left:615px">HUMAN SERVICES</div>
<div class="svc-label" style="left:885px">SPIRITUAL NEEDS</div>

<svg class="abs" style="left:0;top:1350px" width="1200" height="700" viewBox="0 0 1200 700"><path d="M0 40 C150 0 270 0 420 25 C560 50 680 5 820 15 C960 25 1080 40 1200 5 L1200 650 C1040 700 880 680 720 655 C560 630 420 640 260 660 C150 675 60 680 0 665Z" fill="#a4dade"/></svg>
<h2 class="h2" style="left:118px;top:1505px"><span class="mark"></span>About Calmora Health<br>Services</h2>
<p class="copy" style="left:76px;top:1614px;width:510px">Nemo enim ipsam voluptatem quia voluptas sit aspernatur aut odit aut fugit, sed quia consequuntur magni dolores eos qui ratione voluptatem sequi nesciunt. Neque porro quisquam est, qui dolorem ipsum quia dolor sit amet, consectetur, adipisci velit, sed quia non numquam eius modi tempora incidunt ut labore et dolore magnam aliquam quaerat voluptatem.</p>
<div class="btn" style="left:75px;top:1856px;width:206px;height:66px;font-size:18px">Read More</div>
<div class="abs" role="img" aria-label="Photo of a young woman and an older woman smiling together in a garden" style="left:615px;top:1483px;width:512px;height:462px;border-radius:6px;background:linear-gradient(135deg,#9fae8a,#c8b8a0 50%,#5b6e45)"></div>

<div class="abs" role="img" aria-label="Photo of colourful wooden peg figures in a row" style="left:75px;top:2155px;width:510px;height:460px;border-radius:6px;background:linear-gradient(90deg,#3a6a8c,#5e8d4a 30%,#c9a66a 50%,#a34b2d 75%,#d77a35)"></div>
<h2 class="h2" style="left:662px;top:2162px"><span class="mark"></span>Why Choose<br>Calmora Health Service</h2>
<p class="copy" style="left:615px;top:2280px;width:520px">Nemo enim ipsam voluptatem quia voluptas sit aspernatur aut odit aut fugit, sed quia consequuntur magni dolores eos qui ratione voluptatem sequi nesciunt. Neque porro quisquam est, qui dolorem ipsum quia dolor sit amet, consectetur, adipisci velit, sed quia non numquam eius modi tempora incidunt ut labore et dolore magnam aliquam quaerat voluptatem.</p>
<div class="btn" style="left:615px;top:2525px;width:207px;height:67px;font-size:18px">Read More</div>

<svg class="abs" style="left:0;top:2680px" width="1200" height="640" viewBox="0 0 1200 640"><path d="M0 40 C180 5 360 0 560 20 C760 40 960 30 1200 0 L1200 600 C1000 640 820 600 620 585 C420 570 220 600 0 615Z" fill="#efefef"/></svg>
<span class="section-mark" style="top:2780px"></span>
<h2 class="section-title" style="top:2800px">Our Success Stories</h2>
<div class="story faded" style="left:0;width:360px">
  <div class="quote-mark">&ldquo;</div>
  <p>&ldquo; Duis aute irure dolor in reprehenderit in voluptate velit esse cillum dolore eu fugiat nulla pariaturenim ipsam voluptatem quia voluptas sit aspernatur..&rdquo;</p>
  <div class="name">Mara Ellison</div>
</div>
<div class="story" style="left:398px;width:380px">
  <div class="quote-mark">&ldquo;</div>
  <p>&ldquo; Duis aute irure dolor in reprehenderit in voluptate velit esse cillum dolore eu fugiat nulla pariaturenim ipsam voluptatem quia voluptas sit aspernatur..&rdquo;</p>
  <div class="name">Mara Ellison</div>
</div>
<div class="story faded" style="left:815px;width:375px">
  <div class="quote-mark">&ldquo;</div>
  <p>&ldquo; Duis aute irure dolor in reprehenderit in voluptate velit esse cillum dolore eu fugiat nulla pariaturenim ipsam voluptatem quia voluptas sit aspernatur..&rdquo;</p>
  <div class="name">Mara Ellison</div>
</div>
<div class="avatar" role="img" aria-label="Portrait photo of a client" style="left:129px;background:linear-gradient(160deg,#e3a07a,#8a4f35)"></div>
<div class="avatar" role="img" aria-label="Portrait photo of a client" style="left:547px"></div>
<div class="avatar" role="img" aria-label="Portrait photo of a client" style="left:963px;background:linear-gradient(160deg,#9cb4a0,#4f6a5a)"></div>
<span class="arrow" style="left:366px;top:2996px">&#8249;</span>
<span class="arrow" style="left:786px;top:2996px">&#8250;</span>

<span class="section-mark" style="top:3380px"></span>
<h2 class="section-title" style="top:3402px">Partners</h2>
<span class="arrow" style="left:34px;top:3508px">&#8249;</span>
<span class="arrow" style="left:1136px;top:3508px">&#8250;</span>
<div class="partner" style="left:77px"><i></i></div>
<div class="partner" style="left:253px"><i></i></div>
<div class="partner" style="left:430px"><i></i></div>
<div class="partner" style="left:606px"><i></i></div>
<div class="partner" style="left:782px"><i></i></div>
<div class="partner" style="left:958px"><i></i></div>

<svg class="abs" style="left:0;top:3655px" width="1200" height="470" viewBox="0 0 1200 470"><path d="M0 30 C200 70 400 60 600 35 C800 10 1000 0 1200 25 L1200 420 C1000 460 800 470 600 440 C400 410 200 420 0 450Z" fill="#0f2247"/></svg>
<span class="section-mark" style="top:3748px"></span>
<h2 class="news-title">Newsletter Sign Up</h2>
<p class="news-text">Nemo enim ipsam voluptatem quia voluptas sit&nbsp; aspernatur aut odit aut fugit, sed quia consequuntur magni dolores eos qui ratione voluptatem sequi nesciunt. Neque porro quisquam est.</p>
<div class="email">Email Address</div>
<div class="btn submit">Submit Now</div>

<div class="foot-brand"><span class="mark"></span><span>Calmora Health<br>Services</span></div>
<p class="copyright">Copyright &copy; 2025 Calmora Health<br>All Rights Reserved</p>
<span class="social" aria-label="Social profile" style="left:112px"></span>
<span class="social" aria-label="Social profile" style="left:152px"></span>
<span class="social" aria-label="Social profile" style="left:192px"></span>
<span class="social" aria-label="Social profile" style="left:238px"></span>
<span class="social" aria-label="Social profile" style="left:286px"></span>
<h3 class="foot-head" style="left:492px;top:4182px">Quick Links</h3>
<ul class="links">
  <li>Home</li><li>About Us</li><li>Services</li><li>Blog</li><li>Careers</li><li>Contact Us</li>
</ul>
<h3 class="foot-head" style="left:767px;top:4190px">Contact Info</h3>
<ul class="contact">
  <li><svg width="16" height="16" viewBox="0 0 24 24"><path fill="#f6a25b" d="M12 2a7 7 0 0 0-7 7c0 5 7 13 7 13s7-8 7-13a7 7 0 0 0-7-7zm0 9.5A2.5 2.5 0 1 1 12 6.5a2.5 2.5 0 0 1 0 5z"/></svg>48 Larkspur Row, Suite 210,<br>Washington DC 20001</li>
  <li><svg width="16" height="16" viewBox="0 0 24 24"><path fill="#f6a25b" d="M6.6 10.8a15.1 15.1 0 0 0 6.6 6.6l2.2-2.2c.3-.3.7-.4 1-.2 1.1.4 2.3.6 3.6.6.6 0 1 .4 1 1V20c0 .6-.4 1-1 1A17 17 0 0 1 3 4c0-.6.4-1 1-1h3.5c.6 0 1 .4 1 1 0 1.3.2 2.5.6 3.6.1.3 0 .7-.2 1z"/></svg>+1-202-555-0147</li>
  <li><svg width="16" height="16" viewBox="0 0 24 24"><path fill="#f6a25b" d="M3 5h18v14H3zm2 2v.5l7 4.5 7-4.5V7z"/></svg>hello@calmorahealth.org</li>
</ul>

</body>
</html>
```